Investment Advisor E-Newsletter Banner Design

I need a banner designed for an email newsletter that will be sent monthly to clients and prospects. We want to see designs that are elegant and use our logo well. The banner should be 922x150px and should go well with the www.tlvbanda.com website. Should include Logo and email and phone number.

Target Market(s)

High net worth investors

Number of Pages Required

1 page

Requirements
Must have
• logo, place for email (info@tlvbanda.com) and phone number (415-297-6180), colors and design that work well with www.tlvbanda.com website

```html
<!DOCTYPE html>
<html lang="en">
<head>
<meta charset="utf-8">
<title>Tilvane Banda – Newsletter Banner</title>
<link rel="stylesheet" href="https://fonts.googleapis.com/css2?family=Montserrat:wght@500;600&display=swap">
<style>
  :root {
    --page-bg: #eceef1;
    --white: #ffffff;
    --ink-navy: #1f1d8f;
    --stripe-navy: #1c1a6e;
    --slate-top: #4b4b4b;
    --slate-bottom: #191919;
    --violet-top: #5752cd;
    --violet-bottom: #2a22a8;
    --text-light: #ffffff;
  }
  * { margin: 0; padding: 0; box-sizing: border-box; }
  html, body {
    width: 1200px;
    height: 1200px;
    overflow: hidden;
    background: var(--page-bg);
    font-family: "Montserrat", Arial, sans-serif;
  }
  .canvas {
    position: relative;
    width: 1200px;
    height: 1200px;
  }
  .banner {
    position: absolute;
    left: 47px;
    top: 510px;
    width: 1106px;
    height: 180px;
    box-shadow: 0 14px 22px rgba(0, 0, 0, 0.18);
  }
  .banner-shapes {
    position: absolute;
    inset: 0;
    width: 100%;
    height: 100%;
    display: block;
  }
  .brand {
    position: absolute;
    left: 22px;
    top: 74px;
    display: flex;
    align-items: center;
    gap: 12px;
  }
  .brand-mark {
    width: 22px;
    height: 22px;
    background: var(--ink-navy);
  }
  .brand-name {
    font-size: 23px;
    font-weight: 600;
    color: var(--ink-navy);
    white-space: nowrap;
  }
  .tagline {
    position: absolute;
    left: 300px;
    width: 460px;
    top: 54px;
    text-align: center;
    color: var(--text-light);
    font-size: 27px;
    font-weight: 500;
    line-height: 34px;
    letter-spacing: 0.2px;
  }
  .contact {
    position: absolute;
    left: 822px;
    top: 48px;
    list-style: none;
    color: var(--text-light);
    font-size: 22px;
    font-weight: 500;
  }
  .contact-item {
    display: flex;
    align-items: center;
    gap: 14px;
    height: 28px;
    margin-bottom: 19px;
  }
  .contact-icon {
    width: 22px;
    height: 22px;
    flex: none;
    fill: var(--text-light);
  }
</style>
</head>
<body>
<main class="canvas">
  <section class="banner" aria-label="Tilvane Banda newsletter banner">
    <svg class="banner-shapes" viewBox="0 0 922 150" preserveAspectRatio="none" aria-hidden="true">
      <defs>
        <linearGradient id="slate-fill" x1="0" y1="0" x2="0" y2="1">
          <stop offset="0" stop-color="var(--slate-top)"/>
          <stop offset="1" stop-color="var(--slate-bottom)"/>
        </linearGradient>
        <linearGradient id="violet-fill" x1="0" y1="0" x2="0" y2="1">
          <stop offset="0" stop-color="var(--violet-top)"/>
          <stop offset="1" stop-color="var(--violet-bottom)"/>
        </linearGradient>
      </defs>
      <polygon class="panel-white" points="0,0 194,0 244,150 0,150" fill="var(--white)"/>
      <polygon class="stripe-left" points="194,0 220,0 250,150 244,150" fill="var(--stripe-navy)"/>
      <polygon class="panel-slate" points="220,0 622,0 657,150 250,150" fill="url(#slate-fill)"/>
      <polygon class="stripe-right" points="622,0 632,0 680,150 657,150" fill="var(--stripe-navy)"/>
      <polygon class="panel-violet" points="632,0 922,0 922,150 680,150" fill="url(#violet-fill)"/>
    </svg>

    <div class="brand">
      <span class="brand-mark" aria-hidden="true"></span>
      <span class="brand-name">Tilvane Banda</span>
    </div>

    <p class="tagline">Evidence-based Investment Management. Personal Service.</p>

    <ul class="contact">
      <li class="contact-item">
        <svg class="contact-icon" viewBox="0 0 24 24" aria-hidden="true">
          <path d="M2 5h20v2l-10 6L2 7z"/>
          <path d="M2 9l10 6 10-6v10H2z"/>
        </svg>
        <span>info@tlvbanda.com</span>
      </li>
      <li class="contact-item">
        <svg class="contact-icon" viewBox="0 0 24 24" aria-hidden="true">
          <path d="M6.6 10.8a15.2 15.2 0 0 0 6.6 6.6l2.2-2.2a1 1 0 0 1 1-.25 11.4 11.4 0 0 0 3.6.57 1 1 0 0 1 1 1V20a1 1 0 0 1-1 1A17 17 0 0 1 3 4a1 1 0 0 1 1-1h3.5a1 1 0 0 1 1 1c0 1.25.2 2.46.57 3.58a1 1 0 0 1-.25 1z"/>
        </svg>
        <span>415-297-6180</span>
      </li>
    </ul>
  </section>
</main>
</body>
</html>
```